High-End Print/Digital Ad for Unique Luxury Travel Company Required

Objective:
Design a compelling and visually striking advertisement that highlights our company’s unmatched luxury travel experiences. The ad should elevate our brand image, spark curiosity, and drive prospective clients to contact us.
Target Audience:
• Affluent individuals seeking extraordinary, tailor-made travel experiences
• Affluent, luxury, high-net-worth individuals looking for value, expertise, and white-glove service
• Professionals or retirees who appreciate unique, thoughtfully curated travel over mainstream tourism
Key Messages to Communicate:
• One-of-a-kind luxury travel: Once-in-a-lifetime experiences that are curated with creativity and meticulous attention to detail
• Exceptional service: White-glove, personalized planning from start to finish
• 38 years’ travel experience – expert knowledge of destinations, modes of travel, premium accommodations and well-established, meaningful industry connections.
• Highly trusted: Cruise line executives often say, “No one does what you do.”
Tone and Style:
• Elegant, luxurious, sophisticated
• Eye-catching, polished, and modern
• Professional but warm—conveys trust and credibility
• High-impact visuals (full-bleed imagery, custom graphics, or high-end photography)
Deliverables:
• One full-page print ad and digital ad
• Ready-to-print, high-resolution file + working file (PSD, AI, etc.)
Optional: Social media-optimized version or short motion-graphic variation (if designer offers it)
Inspiration & Visual Style Suggestions:
• Think Lumen Voyages, Harrow Pike Wanderer, Silver Quill, or Orvel Retreats ad styles
• Large, emotive imagery with elegant typography
• Clean layout that speaks luxury, clarity, and trust
Copy Direction (draft):
For those who’ve explored the world—and crave something beyond the ordinary.
Each journey is a masterfully curated experience, rich in detail, seamless in execution, and unforgettable in every way.
Founded in 1997, Tidewell Journeys is a unique travel company specializing in cruising, all-inclusive luxury properties, and tours world-wide for individuals, groups, and incentives.
We offer an exceptional range of services designed to ensure every journey is flawlessly executed and truly unforgettable.
Let us help you plan your next extraordinary adventure.
Note: You may refine the copy slightly based on layout or format needs.
Other Resources for References:
1. Website - www.tidewelljourneys-example.com

```html
<!DOCTYPE html>
<html lang="en">
<head>
<meta charset="utf-8">
<title>Tidewell Journeys – Campaign Formats</title>
<link href="https://fonts.googleapis.com/css2?family=Montserrat:wght@400;500&display=swap" rel="stylesheet">
<style>
  :root {
    --board-bg: #dedede;
    --navy: #17468f;
    --label-ink: #4a4f57;
    --rule: #55595f;
    --sky-light: #eef8f8;
    --sky-mid: #a9d4df;
    --sky-deep: #5f9fbd;
    --sea: #4f8fae;
    --dress: #f7b150;
    --dress-soft: #fbd7a0;
  }
  * { margin: 0; padding: 0; box-sizing: border-box; }
  html, body {
    width: 1200px; height: 800px; overflow: hidden;
    background: var(--board-bg);
    font-family: "Montserrat", Arial, sans-serif;
  }
  .board { position: relative; width: 1200px; height: 800px; }

  .connectors { position: absolute; inset: 0; }

  .format-label {
    position: absolute; right: 47px;
    font-size: 15px; font-weight: 400; letter-spacing: 0.5px;
    color: var(--label-ink); line-height: 1;
  }
  .format-label--print { top: 50px; }
  .format-label--social { top: 85px; }
  .format-label--banner { top: 119px; }

  .ad { position: absolute; overflow: hidden; }
  .ad__photo {
    position: absolute; inset: 0;
    background:
      radial-gradient(ellipse 45% 50% at 52% 72%, var(--dress) 0%, var(--dress-soft) 45%, rgba(251,215,160,0) 75%),
      linear-gradient(180deg, rgba(0,0,0,0) 0%, rgba(0,0,0,0) 62%, var(--sea) 100%),
      linear-gradient(120deg, var(--sky-light) 0%, var(--sky-light) 25%, var(--sky-mid) 55%, var(--sky-deep) 100%);
  }
  .ad__copy { position: absolute; color: var(--navy); }
  .ad__headline { font-weight: 400; letter-spacing: -0.3px; }
  .ad__subhead { font-weight: 400; }
  .ad__rule { border: 0; border-top: 1px solid var(--navy); }
  .ad__body { font-weight: 500; }

  .brand {
    position: absolute; display: flex; align-items: center;
    color: var(--navy); font-weight: 500; white-space: nowrap;
  }
  .brand__dot { border-radius: 50%; background: var(--navy); flex: none; }

  /* Print */
  .ad--print { left: 42px; top: 41px; width: 510px; height: 718px; }
  .ad--print .ad__copy { left: 29px; top: 22px; }
  .ad--print .ad__headline { font-size: 38px; line-height: 38px; }
  .ad--print .ad__subhead { font-size: 18.5px; line-height: 20px; margin-top: 3px; }
  .ad--print .ad__rule { width: 149px; margin: 9px 0 0 0; }
  .ad--print .ad__body { font-size: 9.3px; line-height: 12.4px; margin-top: 8px; }
  .ad--print .brand { right: 16px; bottom: 20px; font-size: 19px; gap: 8px; }
  .ad--print .brand__dot { width: 20px; height: 20px; }

  /* Banner */
  .ad--banner { left: 781px; top: 203px; width: 372px; height: 141px; }
  .ad--banner .ad__copy { left: 10px; top: 13px; }
  .ad--banner .ad__headline { font-size: 22px; line-height: 22.5px; }
  .ad--banner .ad__subhead { font-size: 10px; line-height: 11.5px; margin-top: 3px; }
  .ad--banner .brand { right: 8px; bottom: 10px; font-size: 9.5px; gap: 4px; }
  .ad--banner .brand__dot { width: 10px; height: 10px; }

  /* Social */
  .ad--social { left: 781px; top: 386px; width: 372px; height: 373px; }
  .ad--social .ad__copy { left: 14px; top: 14px; }
  .ad--social .ad__headline { font-size: 26px; line-height: 26px; }
  .ad--social .ad__subhead { font-size: 12px; line-height: 13.5px; margin-top: 4px; }
  .ad--social .brand { right: 14px; bottom: 15px; font-size: 12.5px; gap: 5px; }
  .ad--social .brand__dot { width: 13px; height: 13px; }
</style>
</head>
<body>
<main class="board">
  <svg class="connectors" width="1200" height="800" viewBox="0 0 1200 800" aria-hidden="true">
    <g fill="none" stroke="var(--rule)" stroke-width="1">
      <line x1="564" y1="58" x2="1066" y2="58"/>
      <polyline points="999,93 699,93 699,398 767,398"/>
      <polyline points="980,127 735,127 735,221 767,221"/>
    </g>
    <g fill="var(--rule)">
      <circle cx="564" cy="58" r="4"/>
      <circle cx="767" cy="398" r="4"/>
      <circle cx="767" cy="221" r="4"/>
    </g>
  </svg>

  <span class="format-label format-label--print">PRINT AD</span>
  <span class="format-label format-label--social">SOCIAL MEDIA AD</span>
  <span class="format-label format-label--banner">DIGITAL BANNER AD</span>

  <section class="ad ad--print">
    <div class="ad__photo" role="img" aria-label="Photograph: woman seen from behind on a sailboat deck, flowing orange chiffon dress, sea and bright cloudy sky"></div>
    <div class="ad__copy">
      <h1 class="ad__headline">For those<br>who’ve explored<br>the world</h1>
      <p class="ad__subhead">and crave something<br>beyond the ordinary.</p>
      <hr class="ad__rule">
      <p class="ad__body">We offer an exceptional range of<br>services designed to ensure every<br>journey is flawlessly executed<br>and truly unforgettable.<br>www.tidewelljourneys-example.com</p>
    </div>
    <div class="brand"><span class="brand__dot"></span>Tidewell Journeys</div>
  </section>

  <section class="ad ad--banner">
    <div class="ad__photo" role="img" aria-label="Photograph: woman in flowing orange dress on a sailboat facing the sea"></div>
    <div class="ad__copy">
      <h2 class="ad__headline">For those<br>who’ve<br>explored<br>the world</h2>
      <p class="ad__subhead">and crave something<br>beyond the ordinary.</p>
    </div>
    <div class="brand"><span class="brand__dot"></span>Tidewell Journeys</div>
  </section>

  <section class="ad ad--social">
    <div class="ad__photo" role="img" aria-label="Photograph: woman in flowing orange dress on a sailboat deck overlooking the sea"></div>
    <div class="ad__copy">
      <h2 class="ad__headline">For those<br>who’ve<br>explored<br>the world</h2>
      <p class="ad__subhead">and crave something<br>beyond the ordinary.</p>
    </div>
    <div class="brand"><span class="brand__dot"></span>Tidewell Journeys</div>
  </section>
</main>
</body>
</html>
```